House-share and Room Rental Website (With Focus on the Bedroom Landing Page)

Looking for website design for our House-share (executive accommodation) and room rental business.

Our company name is: Lodgivo could also be written as LodGivo or lodgivo. Either is fine .. just looking for a nice clean catchy logo to go with the design.

EXAMPLES
These are examples of other websites in this field that are doing well. this is a kind of baseline.
https://nestpartners-example.com.au/
https://www.bunkora-example.com/
https://www.dwelzy-example.com/
https://www.habiquo-example.net/
https://www.cohabiscout-example.com.au/

Our business model is to rent rooms to people looking for high-quality accommodation. We fill the gap between those looking to rent rooms and those with rooms to rent. However, our model is slightly different from those already on the market as we looking to fill a massive gap in the market delivering upmarket rooms for rent.(Executive Accommodation) also in the back end will be coupled with a self management process in the back end.

We offer executive style accommodation that stands out above the rest. With special extras like fire safety.. and management processes that create happier homes. We are looking for a web design package that can help us grow and scale our business. We need a design that is captivating

Our MAIN focus is having a room landing page that stands out from the rest... The core of our business will rely on the promotion of the rooms in a share house... so the whole design relies on the BEDROOM landing page to drive results.

Target Market(s)

We have 2 markets we are aiming at ... the first market is people offering rooms to rent who want the highest rental return. The second market is people looking to rent safe, high-quality rooms, in houses that are well managed and looked after.

Industry/Entity Type

Share Economy

Logo Text

LodGivo

Number of Pages Required

5+ page

Font styles to use
Sans Serif

Colors
3276b5

Requirements
Must have
• A messaging system whereby we can create direct communication between those offering rooms and those looking for rooms.
• A call to action that says " Schedule an Inspection"
• Landing page for promoting rooms
• A home page for showing stock.
• Profile page for those selling rooms
• Profile page for those looking for rooms.
• A scheduling calendar for booking inspections
Nice to have
• Pages where new residents can lock in a room.. pay bond and rents.. and sign contracts
• Notifications
• SMS capabilities in the backend.
Should not have
• No script or handwriting fonts.

```html
<!DOCTYPE html>
<html lang="en">
<head>
<meta charset="utf-8">
<title>Lodgivo – Luxurious &amp; Stunning Room</title>
<link href="https://fonts.googleapis.com/css2?family=Questrial&family=Open+Sans:wght@400;600;700&display=swap" rel="stylesheet">
<style>
:root{
  --blue:#1f74c0;
  --blue-dark:#165d9c;
  --ink:#222;
  --text:#444;
  --muted:#777;
  --line:#dedede;
  --page:#f7f7f7;
  --card:#fff;
  --dark:#2b2b2b;
  --footer:#232323;
  --gold:#f2b705;
}
*{box-sizing:border-box;margin:0;padding:0}
html,body{width:1200px;height:3579px;overflow:hidden}
body{position:relative;background:var(--page);font-family:"Open Sans",Arial,sans-serif;color:var(--text);font-size:13px}
.abs{position:absolute}
.heading{font-family:"Questrial","Century Gothic",sans-serif;color:var(--ink)}
.blue{color:var(--blue)}
.divider{position:absolute;left:79px;width:1040px;height:1px;background:var(--line)}
.stars{color:var(--gold);letter-spacing:1px}
.link-more{font-size:12px;color:var(--ink)}
.link-more svg{vertical-align:middle;margin-left:3px}

/* header */
.site-header{position:absolute;left:0;top:0;width:1200px;height:72px;background:#fff}
.menu-grid{left:79px;top:36px}
.lang{left:111px;top:35px;font-size:11px;color:var(--ink)}
.lang .flag{display:inline-block;width:14px;height:9px;background:linear-gradient(#b22 0 50%,#fff 50%);vertical-align:middle;margin-right:4px}
.brand{display:flex;align-items:center;gap:8px}
.brand .mark{width:22px;height:22px;border-radius:50%;background:var(--blue)}
.brand .name{font-family:"Questrial",sans-serif;font-size:30px;color:var(--blue)}
.site-header .brand{position:absolute;left:510px;top:16px}
.btn{display:inline-flex;align-items:center;justify-content:center;border-radius:4px;font-size:12px}
.btn-primary{background:var(--blue);color:#fff}
.btn-ghost{border:1px solid #aaa;color:var(--ink);background:#fff}

/* hero */
.photo{background:linear-gradient(135deg,#6b5444,#b89c78 45%,#d9c7a6 60%,#5a4637)}
.hero-photo{left:79px;top:100px;width:522px;height:349px}
.room-kicker{font-size:13px;color:var(--ink)}
.room-title{font-size:29px;color:var(--blue);font-weight:700;font-family:"Open Sans",sans-serif;letter-spacing:-.2px}
.address{font-size:13px;color:var(--ink);display:flex;align-items:center;gap:6px}
.facts{display:flex;gap:40px}
.fact{font-size:12px;color:var(--ink)}
.fact .row{display:flex;align-items:center;gap:3px}
.lead{font-size:13px;line-height:18px;color:var(--ink)}

/* amenities */
.section-title{font-family:"Questrial",sans-serif;font-size:29px;color:var(--ink)}
.sub{font-size:12px;color:var(--ink)}
.amenity{position:absolute;font-size:11.5px;color:var(--ink)}
.amenity svg{display:block;margin-bottom:6px}
.sleep-card{left:79px;top:878px;width:148px;height:88px;background:#fff;padding:12px;font-size:11.5px;line-height:15px;color:var(--ink)}

/* booking */
.booking{left:635px;top:484px;width:484px;height:458px;background:var(--card);box-shadow:0 1px 5px rgba(0,0,0,.08)}
.booking .inner{position:absolute;left:29px;right:29px}
.price{font-size:33px;font-weight:700;color:var(--ink)}
.price small{font-size:11px;font-weight:400}
.b-line{position:absolute;left:0;width:100%;height:1px;background:var(--line)}
.b-label{font-size:17px;color:var(--ink);font-family:"Questrial",sans-serif}
.select{height:46px;border:1px solid #ccc;border-radius:6px;display:flex;align-items:center;justify-content:space-between;padding:0 18px;font-size:12px;color:var(--ink)}

/* calendar */
.calendar{width:498px;border-collapse:collapse;background:#fff;table-layout:fixed}
.calendar caption{background:var(--dark);color:#fff;height:48px;line-height:48px;font-family:"Questrial",sans-serif;font-size:29px;border-radius:8px 8px 0 0}
.calendar th{height:31px;font-weight:400;font-size:12px;color:var(--ink);border:1px solid var(--line)}
.calendar td{height:44px;text-align:center;font-size:13px;color:var(--ink);border:1px solid var(--line)}
.calendar td.booked{background:var(--blue);color:#fff}
.arrow-nav{display:flex;gap:20px}

/* reviews */
.rating-row{position:absolute;width:520px;display:flex;justify-content:space-between;font-size:11.5px;color:var(--ink);border-bottom:1px solid var(--line);padding-bottom:3px}
.rating-row .stars{font-size:11px}
.field{position:absolute;background:#fff;border:1px solid #ddd;border-radius:4px;display:flex;align-items:center;padding:0 12px;font-size:12px;color:var(--ink);gap:8px}
.avatar{position:absolute;width:95px;height:95px;border-radius:50%;background:linear-gradient(#b9a08a,#7c6250)}
.reviewer{font-size:19px;color:var(--ink);font-family:"Questrial",sans-serif}
.review-date{font-size:12px;color:var(--ink)}
.review-text{font-size:12.5px;line-height:17px;color:var(--ink)}
.pager{left:0;width:1200px;top:1962px;display:flex;justify-content:center;gap:20px;font-size:13px;color:var(--ink)}
.pager .on{color:var(--blue);border-bottom:2px solid var(--blue)}

/* neighborhood */
.map{left:79px;top:2207px;width:522px;height:243px;background:linear-gradient(120deg,#8fb8e0,#aacde9 30%,#c8d8a8 50%,#98bde0 75%,#b9c99a)}
.rule-title{font-size:19px;font-weight:700;color:var(--blue)}
.small-lines{font-size:11.5px;line-height:16px;color:var(--ink)}

/* similar */
.room-card{position:absolute;top:2653px;width:327px;height:413px;background:#fff;box-shadow:0 1px 5px rgba(0,0,0,.08)}
.room-card .photo{position:absolute;left:0;top:0;width:100%;height:215px}
.room-card .badge{position:absolute;left:0;top:155px;background:var(--blue);color:#fff;font-weight:700;font-size:20px;padding:6px 14px;border-radius:0 20px 20px 0}
.room-card .check{position:absolute;left:8px;top:8px;width:18px;height:18px;background:rgba(255,255,255,.85);border-radius:3px}
.room-card .title{position:absolute;left:18px;top:232px;font-size:16px;font-weight:700;color:var(--blue)}
.room-card .address{position:absolute;left:18px;top:278px;font-size:12.5px}
.room-card .facts{position:absolute;left:35px;top:306px;gap:72px}
.room-card .browse{position:absolute;left:115px;top:370px;width:100px;height:31px;background:var(--dark);color:#fff;border-radius:4px;font-size:12px;display:flex;align-items:center;justify-content:center}

/* footer */
.site-footer{position:absolute;left:0;top:3161px;width:1200px;height:351px;background:var(--footer);color:#eee}
.site-footer .brand .name{color:var(--blue)}
.f-head{font-size:17px;color:#fff;font-family:"Questrial",sans-serif}
.f-text{font-size:13px;line-height:20px;color:#eee}
.f-links li{list-style:none;font-size:12px;line-height:20.5px;color:#fff}
.f-links li::before{content:"›";margin-right:12px}
.social{display:flex;gap:8px}
.social span{width:22px;height:22px;border-radius:50%;background:var(--blue);display:block}
.contact-row{display:flex;gap:12px;align-items:flex-start;font-size:13px;line-height:19px;color:#eee}
.f-input{position:absolute;background:#3a3a3a;color:#ddd;font-size:12px;padding:6px 10px}
.copy-bar{position:absolute;left:0;top:3512px;width:1200px;height:67px;background:var(--blue);color:#fff;font-size:12px}
.cards{display:flex;gap:8px}
.cards span{width:36px;height:22px;background:#fff;border-radius:3px;display:block}
</style>
</head>
<body>

<header class="site-header">
  <svg class="abs menu-grid" width="22" height="22" viewBox="0 0 22 22"><g fill="#444"><rect x="0" y="0" width="5" height="5"/><rect x="8" y="0" width="5" height="5"/><rect x="16" y="0" width="5" height="5"/><rect x="0" y="8" width="5" height="5"/><rect x="8" y="8" width="5" height="5"/><rect x="16" y="8" width="5" height="5"/><rect x="0" y="16" width="5" height="5"/><rect x="8" y="16" width="5" height="5"/><rect x="16" y="16" width="5" height="5"/></g></svg>
  <div class="abs lang"><span class="flag"></span>Eng ▾</div>
  <div class="brand"><span class="mark"></span><span class="name">Lodgivo</span></div>
  <a class="abs btn btn-primary" style="left:918px;top:30px;width:127px;height:29px">Post Your Room</a>
  <a class="abs btn btn-ghost" style="left:1064px;top:30px;width:55px;height:29px">Log in</a>
</header>

<!-- room intro -->
<div class="abs photo hero-photo" role="img" aria-label="Photo of a luxurious bedroom with a large bed and arched windows"></div>
<div class="abs room-kicker" style="left:637px;top:106px">Luxurious Room</div>
<h1 class="abs room-title" style="left:637px;top:122px">Luxurious &amp; Stunning Room</h1>
<div class="abs address" style="left:637px;top:166px">
  <svg width="12" height="16" viewBox="0 0 12 16"><path d="M6 0a6 6 0 0 0-6 6c0 4.5 6 10 6 10s6-5.5 6-10a6 6 0 0 0-6-6zm0 8.5A2.5 2.5 0 1 1 6 3.5a2.5 2.5 0 0 1 0 5z" fill="#555"/></svg>
  18 Harbourline Road, Kelmsworth, Australia</div>
<div class="abs room-kicker" style="left:637px;top:213px">Luxurious Room</div>
<div class="abs facts" style="left:637px;top:254px">
  <div class="fact"><div class="row"><svg width="22" height="20" viewBox="0 0 22 20"><path d="M2 9 11 2l9 7v10H2z" fill="none" stroke="#333" stroke-width="2"/><rect x="7" y="12" width="8" height="5" fill="#333"/></svg><small>2</small></div>Rooms</div>
  <div class="fact"><div class="row"><svg width="24" height="18" viewBox="0 0 24 18"><rect x="1" y="8" width="22" height="6" fill="#333"/><rect x="3" y="3" width="7" height="5" fill="#333"/><rect x="1" y="14" width="2" height="4" fill="#333"/><rect x="21" y="14" width="2" height="4" fill="#333"/></svg><small>4</small></div>Bed</div>
  <div class="fact"><div class="row"><svg width="22" height="20" viewBox="0 0 22 20"><path d="M1 10h20v4a4 4 0 0 1-4 4H5a4 4 0 0 1-4-4z" fill="#333"/><path d="M4 10V3a2 2 0 0 1 4 0" fill="none" stroke="#333" stroke-width="2"/></svg><small>2</small></div>Bath</div>
</div>
<p class="abs lead" style="left:637px;top:324px;width:482px">Lorem Ipsum is simply dummy text of the printing and typesetting industry. Lorem Ipsum has been the industry's standard dummy text ever since the 1500s, when an unknown printer took a galley of type and scrambled it to make a type specimen book.</p>
<div class="abs link-more" style="left:637px;top:410px">Read more<svg width="10" height="6" viewBox="0 0 10 6"><path d="M1 1l4 4 4-4" fill="none" stroke="#333" stroke-width="1.5"/></svg></div>

<!-- amenities -->
<h2 class="abs section-title" style="left:79px;top:485px">ROOM amenities (not limited to)</h2>
<div class="abs sub" style="left:79px;top:522px">these are some things that may be included in the room</div>
<div class="amenity" style="left:84px;top:590px"><svg width="26" height="24" viewBox="0 0 26 24"><rect x="2" y="8" width="22" height="10" fill="#333"/><rect x="0" y="6" width="4" height="14" fill="#333"/><rect x="22" y="6" width="4" height="14" fill="#333"/></svg>Furnished/unfurnished</div>
<div class="amenity" style="left:250px;top:580px"><svg width="26" height="30" viewBox="0 0 26 30"><path d="M8 2l5 6 5-6" fill="none" stroke="#333" stroke-width="2"/><rect x="1" y="8" width="24" height="18" rx="2" fill="none" stroke="#333" stroke-width="2.5"/><text x="7" y="21" font-size="9" font-family="Arial" fill="#333">TV</text></svg>TV</div>
<div class="amenity" style="left:370px;top:580px"><svg width="30" height="30" viewBox="0 0 30 30"><rect x="2" y="14" width="26" height="3" fill="#333"/><rect x="4" y="17" width="3" height="12" fill="#333"/><rect x="20" y="17" width="7" height="12" fill="#333"/><rect x="9" y="3" width="12" height="9" fill="#333"/></svg>Study Desk</div>
<div class="amenity" style="left:501px;top:580px"><svg width="28" height="30" viewBox="0 0 28 30"><rect x="1" y="8" width="26" height="20" fill="#333"/><rect x="5" y="2" width="4" height="6" fill="#333"/><rect x="17" y="2" width="6" height="6" fill="#333"/><rect x="4" y="12" width="9" height="6" fill="#fff"/><rect x="15" y="12" width="9" height="6" fill="#fff"/></svg>Kitchen</div>
<div class="amenity" style="left:84px;top:700px"><svg width="26" height="30" viewBox="0 0 26 30"><rect x="1" y="1" width="24" height="28" fill="#333"/><circle cx="13" cy="8" r="4" fill="#fff"/><path d="M8 16v8M13 16v10M18 16v8" stroke="#fff" stroke-width="1.5"/></svg>Ensuite shower</div>
<div class="amenity" style="left:250px;top:700px"><svg width="24" height="32" viewBox="0 0 24 32"><rect x="1" y="1" width="22" height="28" fill="none" stroke="#333" stroke-width="2"/><line x1="12" y1="1" x2="12" y2="29" stroke="#333" stroke-width="2"/><rect x="3" y="29" width="3" height="3" fill="#333"/><rect x="18" y="29" width="3" height="3" fill="#333"/></svg>Wardrobe</div>
<div class="amenity" style="left:370px;top:700px"><svg width="28" height="28" viewBox="0 0 28 28"><rect x="1" y="1" width="26" height="26" fill="#333"/><rect x="5" y="5" width="8" height="8" fill="#fff"/><rect x="15" y="15" width="8" height="8" fill="#fff"/></svg>Storage space</div>
<div class="divider" style="top:804px;width:522px"></div>
<h2 class="abs section-title" style="left:79px;top:830px">Sleeping arrangements</h2>
<div class="abs sleep-card"><svg width="24" height="16" viewBox="0 0 24 16"><rect x="1" y="7" width="22" height="6" fill="#333"/><rect x="3" y="2" width="7" height="5" fill="#333"/><rect x="1" y="13" width="2" height="3" fill="#333"/><rect x="21" y="13" width="2" height="3" fill="#333"/></svg><br>Bedroom 2<br>2 queen bed, 2 Full</div>

<!-- booking card -->
<aside class="abs booking">
  <div class="inner" style="top:26px"><span class="price">$250</span> <small style="font-size:11px;color:#333">Per night</small></div>
  <div class="inner" style="top:68px;font-size:11px"><span class="stars">★★★★★</span> 43</div>
  <div class="b-line" style="top:110px"></div>
  <div class="inner b-label" style="top:136px">Dates</div>
  <div class="inner" style="top:162px;font-size:11px;color:#333;display:flex;gap:120px"><span>Check in &nbsp;▭</span><span>Check out &nbsp;▭</span></div>
  <div class="b-line" style="top:206px"></div>
  <div class="inner b-label" style="top:222px">Guests</div>
  <div class="inner select" style="top:265px"><span>3 Guests</span><svg width="12" height="8" viewBox="0 0 12 8"><path d="M1 1l5 5 5-5" fill="none" stroke="#333" stroke-width="1.6"/></svg></div>
  <div class="inner btn btn-primary" style="top:349px;height:40px;font-size:12px">Book now</div>
  <div class="inner" style="top:400px;text-align:center;font-size:12px;color:#333">Lorem Ipsum is simply dummy text of the printing.</div>
</aside>
<div class="abs" style="left:810px;top:956px;font-size:12px;color:var(--ink);display:flex;align-items:center;gap:6px"><svg width="12" height="14" viewBox="0 0 12 14"><path d="M1 14V1h9l-2 3 2 3H1" fill="none" stroke="#333" stroke-width="1.5"/></svg>Report this listing</div>

<div class="divider" style="top:1000px"></div>

<!-- availability -->
<h2 class="abs section-title" style="left:79px;top:1028px">Availability</h2>
<div class="abs sub" style="left:79px;top:1068px">Updated 6 days ago</div>
<div class="abs arrow-nav" style="left:1068px;top:1074px">
  <svg width="12" height="18" viewBox="0 0 12 18"><path d="M10 2 3 9l7 7" fill="none" stroke="#222" stroke-width="3"/></svg>
  <svg width="12" height="18" viewBox="0 0 12 18"><path d="M2 2l7 7-7 7" fill="none" stroke="var(--blue)" stroke-width="3"/></svg>
</div>

<table class="abs calendar" style="left:79px;top:1114px">
  <caption>January</caption>
  <tr><th>Sun</th><th>Mon</th><th>Tue</th><th>Wed</th><th>Thu</th><th>Fri</th><th>Sat</th></tr>
  <tr><td></td><td></td><td>1</td><td>2</td><td>3</td><td>4</td><td>5</td></tr>
  <tr><td>6</td><td>7</td><td>8</td><td>9</td><td>10</td><td>11</td><td class="booked">12</td></tr>
  <tr><td class="booked">13</td><td class="booked">14</td><td>15</td><td>16</td><td>17</td><td>18</td><td>19</td></tr>
  <tr><td>20</td><td>21</td><td>22</td><td>23</td><td>24</td><td>25</td><td>26</td></tr>
  <tr><td>27</td><td>28</td><td>29</td><td>30</td><td>31</td><td></td><td></td></tr>
</table>
<table class="abs calendar" style="left:621px;top:1114px">
  <caption>February</caption>
  <tr><th>Sun</th><th>Mon</th><th>Tue</th><th>Wed</th><th>Thu</th><th>Fri</th><th>Sat</th></tr>
  <tr><td></td><td></td><td>1</td><td>2</td><td>3</td><td>4</td><td>5</td></tr>
  <tr><td>6</td><td>7</td><td>8</td><td>9</td><td>10</td><td>11</td><td>12</td></tr>
  <tr><td>13</td><td>14</td><td>15</td><td>16</td><td>17</td><td>18</td><td>19</td></tr>
  <tr><td>20</td><td class="booked">21</td><td class="booked">22</td><td class="booked">23</td><td class="booked">24</td><td class="booked">25</td><td>26</td></tr>
  <tr><td>27</td><td>28</td><td></td><td></td><td></td><td></td><td></td></tr>
</table>

<div class="divider" style="top:1448px"></div>

<!-- reviews -->
<h2 class="abs section-title" style="left:79px;top:1480px">Reviews <span class="stars" style="font-size:15px;vertical-align:middle">★★★★★</span> <span style="font-size:13px;vertical-align:middle">( 43 )</span></h2>
<div class="rating-row" style="left:79px;top:1536px"><span>Accuracy</span><span class="stars">★★★★★</span></div>
<div class="rating-row" style="left:79px;top:1558px"><span>Communication</span><span class="stars">★★★★★</span></div>
<div class="rating-row" style="left:79px;top:1580px"><span>Cleanliness</span><span class="stars">★★★★★</span></div>
<div class="rating-row" style="left:639px;top:1536px;width:470px"><span>Location</span><span class="stars">★★★★★</span></div>
<div class="rating-row" style="left:639px;top:1558px;width:470px"><span>Check-in</span><span class="stars">★★★★★</span></div>
<div class="rating-row" style="left:639px;top:1580px;width:470px"><span>Value</span><span class="stars">★★★★☆</span></div>
<div class="field" style="left:79px;top:1622px;width:274px;height:34px"><svg width="12" height="12" viewBox="0 0 12 12"><circle cx="5" cy="5" r="4" fill="none" stroke="#333" stroke-width="1.5"/><path d="M8 8l3 3" stroke="#333" stroke-width="1.5"/></svg>Search reviews</div>
<div class="field" style="left:918px;top:1622px;width:194px;height:34px;justify-content:space-between">Most revelant<svg width="10" height="6" viewBox="0 0 10 6"><path d="M1 1l4 4 4-4" fill="none" stroke="#333" stroke-width="1.5"/></svg></div>

<div class="divider" style="top:1692px"></div>

<div class="avatar" style="left:84px;top:1730px" role="img" aria-label="Reviewer portrait photo"></div>
<div class="abs reviewer" style="left:191px;top:1746px">Nora Vell</div>
<div class="abs review-date" style="left:191px;top:1774px">21.January</div>
<svg class="abs" style="left:560px;top:1752px" width="13" height="14" viewBox="0 0 13 14"><path d="M1 14V1h10l-2 3 2 3H1" fill="none" stroke="#333" stroke-width="1.5"/></svg>
<p class="abs review-text" style="left:79px;top:1838px;width:510px">Lorem Ipsum is simply dummy text of the printing and typesetting industry. Lorem Ipsum has been the industry's standard dummy text ever since the 1500s, when an unknown printer took a galley of type and scrambled it to make a type specimen book.</p>

<div class="avatar" style="left:621px;top:1730px" role="img" aria-label="Reviewer portrait photo"></div>
<div class="abs reviewer" style="left:734px;top:1746px">Tobias Renn</div>
<div class="abs review-date" style="left:734px;top:1774px">2.February</div>
<svg class="abs" style="left:1098px;top:1752px" width="13" height="14" viewBox="0 0 13 14"><path d="M1 14V1h10l-2 3 2 3H1" fill="none" stroke="#333" stroke-width="1.5"/></svg>
<p class="abs review-text" style="left:618px;top:1838px;width:500px">Lorem Ipsum is simply dummy text of the printing and typesetting industry. Lorem Ipsum has been the industry's standard dummy text ever since the 1500s, when an unknown printer took a galley of type and scrambled it to make a type specimen book.</p>

<div class="abs pager"><span>‹</span><span class="on">1</span><span>2</span><span>3</span><span>4</span><span>5</span><span>6</span><span>.......</span><span class="blue">›</span></div>

<div class="divider" style="top:2021px"></div>

<!-- neighborhood & policies -->
<h2 class="abs section-title" style="left:79px;top:2066px">The neighborhood</h2>
<p class="abs small-lines" style="left:79px;top:2130px;width:510px;font-size:12.5px">Lorem Ipsum is simply dummy text of the printing and typesetting industry. Lorem Ipsum has been the industry's standard dummy text ever since the 1500s.</p>
<div class="abs link-more" style="left:79px;top:2171px">Read more<svg width="10" height="6" viewBox="0 0 10 6"><path d="M1 1l4 4 4-4" fill="none" stroke="#333" stroke-width="1.5"/></svg></div>
<div class="abs map" role="img" aria-label="Map showing the area around the room"></div>

<h2 class="abs section-title" style="left:621px;top:2066px">Policies</h2>
<div class="abs rule-title" style="left:621px;top:2130px">House Rules</div>
<p class="abs small-lines" style="left:621px;top:2160px;width:490px">No pets<br>No smoking, parties, or events<br>Check-in is anytime after 2PM and check out by 1PM</p>
<div class="abs link-more" style="left:624px;top:2236px;font-size:11.5px">Read All Rules<svg width="10" height="6" viewBox="0 0 10 6"><path d="M1 1l4 4 4-4" fill="none" stroke="#333" stroke-width="1.5"/></svg></div>
<div class="divider" style="top:2298px;left:621px;width:498px"></div>
<h2 class="abs section-title" style="left:621px;top:2334px">Cancellations</h2>
<p class="abs small-lines" style="left:621px;top:2378px;width:498px">Strict - Free cancellation for 48 hours<br>After that, cancel up to 7 days before check-in and get a 50% refund, minus the service fee.</p>
<div class="abs link-more" style="left:624px;top:2428px;font-size:11.5px">Read All About the Policies<svg width="10" height="6" viewBox="0 0 10 6"><path d="M1 1l4 4 4-4" fill="none" stroke="#333" stroke-width="1.5"/></svg></div>

<div class="divider" style="top:2510px"></div>

<!-- similar bedrooms -->
<h2 class="abs section-title" style="left:0;width:1200px;text-align:center;top:2553px">Similiar Bedrooms</h2>
<div class="abs arrow-nav" style="left:1068px;top:2608px">
  <svg width="12" height="18" viewBox="0 0 12 18"><path d="M10 2 3 9l7 7" fill="none" stroke="#222" stroke-width="3"/></svg>
  <svg width="12" height="18" viewBox="0 0 12 18"><path d="M2 2l7 7-7 7" fill="none" stroke="var(--blue)" stroke-width="3"/></svg>
</div>

<article class="room-card" style="left:79px">
  <div class="photo" role="img" aria-label="Bright bedroom with canopy bed" style="background:linear-gradient(135deg,#e9e3da,#c9b9a4 50%,#d98a4a 80%,#efe9e2)"></div>
  <span class="check"></span><span class="badge">$250</span>
  <div class="title">Luxurious &amp; Stunning Room</div>
  <div class="address"><svg width="11" height="14" viewBox="0 0 12 16"><path d="M6 0a6 6 0 0 0-6 6c0 4.5 6 10 6 10s6-5.5 6-10a6 6 0 0 0-6-6zm0 8.5A2.5 2.5 0 1 1 6 3.5a2.5 2.5 0 0 1 0 5z" fill="#555"/></svg>18 Harbourline Road, Kelmsworth, Australia</div>
  <div class="facts"><div class="fact">▣<small>2</small><br>Rooms</div><div class="fact">▬<small>4</small><br>Bedrooms</div><div class="fact">◒<small>2</small><br>Bath</div></div>
  <div class="browse">Browse</div>
</article>
<article class="room-card" style="left:434px">
  <div class="photo" role="img" aria-label="Ornate bedroom with carved wooden bed" style="background:linear-gradient(135deg,#3c2b22,#8a6a4e 45%,#c7b59a 65%,#4a382c)"></div>
  <span class="check"></span><span class="badge">$250</span>
  <div class="title">Luxurious &amp; Stunning Room</div>
  <div class="address"><svg width="11" height="14" viewBox="0 0 12 16"><path d="M6 0a6 6 0 0 0-6 6c0 4.5 6 10 6 10s6-5.5 6-10a6 6 0 0 0-6-6zm0 8.5A2.5 2.5 0 1 1 6 3.5a2.5 2.5 0 0 1 0 5z" fill="#555"/></svg>18 Harbourline Road, Kelmsworth, Australia</div>
  <div class="facts"><div class="fact">▣<small>2</small><br>Rooms</div><div class="fact">▬<small>4</small><br>Bedrooms</div><div class="fact">◒<small>2</small><br>Bath</div></div>
  <div class="browse">Browse</div>
</article>
<article class="room-card" style="left:792px">
  <div class="photo" role="img" aria-label="Classic bedroom with red bedspread" style="background:linear-gradient(135deg,#e6d3b5,#b9574a 55%,#8c3b32 75%,#d8c3a0)"></div>
  <span class="check"></span><span class="badge">$250</span>
  <div class="title">Luxurious &amp; Stunning Room</div>
  <div class="address"><svg width="11" height="14" viewBox="0 0 12 16"><path d="M6 0a6 6 0 0 0-6 6c0 4.5 6 10 6 10s6-5.5 6-10a6 6 0 0 0-6-6zm0 8.5A2.5 2.5 0 1 1 6 3.5a2.5 2.5 0 0 1 0 5z" fill="#555"/></svg>18 Harbourline Road, Kelmsworth, Australia</div>
  <div class="facts"><div class="fact">▣<small>2</small><br>Rooms</div><div class="fact">▬<small>4</small><br>Bedrooms</div><div class="fact">◒<small>2</small><br>Bath</div></div>
  <div class="browse">Browse</div>
</article>

<!-- footer -->
<footer class="site-footer">
  <div class="abs brand" style="left:79px;top:80px"><span class="mark"></span><span class="name">Lodgivo</span></div>
  <p class="abs f-text" style="left:79px;top:162px;width:215px">Lorem Ipsum is simply dummy text of the printing and types tysetting industry...</p>
  <div class="abs social" style="left:79px;top:250px"><span></span><span></span><span></span><span></span><span></span></div>

  <div class="abs f-head" style="left:372px;top:74px">Useful links</div>
  <ul class="abs f-links" style="left:372px;top:134px">
    <li>Login</li><li>Register</li><li>My Profile</li><li>My Subscription</li><li>Privacy policy</li><li>Terms &amp; Conditions</li>
  </ul>

  <div class="abs f-head" style="left:577px;top:72px">Contact us</div>
  <div class="abs contact-row" style="left:577px;top:125px"><svg width="16" height="14" viewBox="0 0 16 14"><path d="M8 1 1 7h2v6h4V9h2v4h4V7h2z" fill="#fff"/></svg><span>7 Wattlebank Place, Corrindale,<br>Western Australia.<br>ZipCode: 60000</span></div>
  <div class="abs contact-row" style="left:577px;top:227px"><svg width="16" height="14" viewBox="0 0 16 14"><path d="M1 5c0-3 14-3 14 0v2h-4V5H5v2H1zM4 8h8l2 5H2z" fill="#fff"/></svg><span>100 200 3000</span></div>
  <div class="abs contact-row" style="left:577px;top:256px"><svg width="16" height="12" viewBox="0 0 16 12"><rect x="1" y="1" width="14" height="10" fill="none" stroke="#fff" stroke-width="1.5"/><path d="M1 1l7 6 7-6" fill="none" stroke="#fff" stroke-width="1.5"/></svg><span>info@Lodgivo.com</span></div>

  <div class="abs f-head" style="left:890px;top:72px">Quick Contact</div>
  <div class="f-input" style="left:890px;top:141px;width:95px;height:29px">Name</div>
  <div class="f-input" style="left:1004px;top:141px;width:115px;height:29px">Phone</div>
  <div class="f-input" style="left:890px;top:177px;width:229px;height:65px">Message</div>
  <div class="abs btn btn-primary" style="left:993px;top:251px;width:126px;height:27px;font-size:13px">Send</div>
</footer>
<div class="copy-bar">
  <span class="abs" style="left:79px;top:24px">CopyRight © 2019 Lodgivo. All Right Reserve</span>
  <div class="abs cards" style="left:912px;top:23px"><span></span><span></span><span></span><span></span></div>
</div>

</body>
</html>
```